Casino with the 'highest winning percentage' needs a stationery design

This is for a casino in Colombo, Sri Lanka and we need a stationery design for business card, letter head and envelope.

Should be very professional, simple and elegant without fancy fonts

Reason: Not fully satisfied with the designs. Need more designs.

Business

• 1. card deck symbol 'CLUBS' in red, or black

2. name in BLOCK CAPITAL LETTERS

3. Preferred font colours are black, white or red

4. Prefer 'professional /elegant' fonts
• SHOULD NOT HAVE ANY OTHER SYMBOL EXCEPT 'CLUBS'

DO NOT PREFER ITALIC FONTS

```html
<!DOCTYPE html>
<html lang="en">
<head>
<meta charset="utf-8">
<title>Harlow's Entertainment – Business Card</title>
<link rel="stylesheet" href="https://fonts.googleapis.com/css2?family=Tinos&family=Arimo:wght@400;700&display=swap">
<style>
  :root {
    --stage: #1f1f21;
    --paper: #f1f1f1;
    --paper-shade: #dcdcdc;
    --ink: #1a1a1a;
    --ink-soft: #3c3c3c;
    --rule: #7a7a7a;
    --night: #2c2c2e;
    --night-deep: #19191a;
    --club-red: #c21a22;
    --club-red-deep: #85080f;
    --white: #ffffff;
  }
  * { box-sizing: border-box; margin: 0; padding: 0; }
  html, body {
    width: 1200px; height: 890px; overflow: hidden;
    background: var(--stage);
  }
  .sheet {
    position: relative; width: 1200px; height: 890px;
    display: flex; justify-content: center; align-items: center; gap: 60px;
  }
  .card {
    position: relative; width: 340px; height: 560px;
    border-radius: 26px; overflow: hidden;
  }

  /* Back: contact side */
  .card--back {
    background: linear-gradient(160deg, var(--white), var(--paper) 55%, var(--paper-shade));
    color: var(--ink);
    text-align: center;
    padding-top: 44px;
  }
  .brand-dot {
    display: block; width: 34px; height: 34px; margin: 0 auto 16px;
    border-radius: 50%; background: var(--club-red);
  }
  .brand-name {
    font-family: "Tinos", serif; font-weight: 400;
    text-transform: uppercase; line-height: 1.1;
  }
  .card--back .brand-name { color: var(--ink-soft); font-size: 27px; }
  .brand-name span { display: block; font-size: 0.62em; letter-spacing: 0.04em; }
  .brand-place {
    font-family: "Tinos", serif; font-size: 11px; letter-spacing: 0.06em;
    margin-top: 8px;
  }
  .person { margin-top: 52px; font-family: "Arimo", sans-serif; }
  .person-name { font-size: 16px; font-weight: 700; letter-spacing: 0.02em; }
  .person-role { font-size: 11.5px; margin-top: 5px; }
  .contact {
    font-family: "Arimo", sans-serif; font-size: 12px; line-height: 1.45;
    margin: 40px auto 0; width: 220px;
  }
  .contact-lines { text-align: left; padding-left: 34px; }
  .contact-lines b { font-weight: 700; }
  .divider { height: 1px; background: var(--rule); margin: 12px 0; }
  .address { font-size: 12px; }
  .web { font-weight: 700; font-size: 12.5px; margin-top: 2px; }

  /* Front: brand side */
  .card--front {
    background: linear-gradient(200deg, var(--night) 0%, var(--night-deep) 100%);
    color: var(--white);
  }
  .front-brand {
    position: absolute; top: 70px; right: 34px; text-align: right;
  }
  .card--front .brand-name { color: var(--white); font-size: 30px; }
  .card--front .brand-place { color: var(--white); text-align: center; }
  .front-art {
    position: absolute; left: 0; right: 0; bottom: 0; height: 270px;
    background: radial-gradient(ellipse at 60% 20%, var(--club-red) 0%, var(--club-red-deep) 80%);
  }
</style>
</head>
<body>
  <main class="sheet">
    <section class="card card--back" aria-label="Business card, contact side">
      <span class="brand-dot"></span>
      <h1 class="brand-name">Harlow's<span>Entertainment</span></h1>
      <p class="brand-place">SRI LANKA</p>

      <div class="person">
        <p class="person-name">MARCUS ELWOOD</p>
        <p class="person-role">General Manager</p>
      </div>

      <div class="contact">
        <p class="contact-lines"><b>Tel:</b> + 94 11 555 0142<br><b>Fax:</b> + 94 11 555 0143</p>
        <div class="divider"></div>
        <p class="address">27, Lotus Grove Avenue<br>Colombo 00300, Sri Lanka</p>
        <div class="divider"></div>
        <p class="web">www.harlowscolombo.lk</p>
      </div>
    </section>

    <section class="card card--front" aria-label="Business card, brand side">
      <div class="front-brand">
        <h2 class="brand-name">Harlow's<span>Entertainment</span></h2>
        <p class="brand-place">SRI LANKA</p>
      </div>
      <div class="front-art" role="img" aria-label="Large glossy red playing-card suit artwork"></div>
    </section>
  </main>
</body>
</html>
```